2 banners on the outside wall of the hall

Banner 1:
KalviMar specializes in the planning, construction, and maintenance of high-quality pond systems, particularly swimming ponds, natural pools, garden ponds, koi ponds, streams, and waterfalls. Learn more at www.kalvimar.de
The following data should be included:
Planning and construction of swimming ponds and natural pools, as well as garden ponds and koi ponds
100% organic
Individually planned
Over 20 years of experience
04627 3150962
www.kalvimar.de
“Logo-KalviMar”
Banner 2:
Grünflut-Laden is the online shop for high-quality aquatic plants for ponds and aquariums.
More information at https://gruenflut-laden.de
Online shop for pond plants and water lilies, as well as aquarium plants and accessories
Over 400 plant species
Top gardener quality
Secure packaging & fast shipping
04627 3150961
www.gruenflut-laden. de
“Logo Greenflow shop”
Here's roughly what we envision:
The designs for each banner should be clearly visible and include everything needed, without appearing cluttered. In other words, it should be immediately clear what the banner is about.
We should also be made aware of our unique selling points and advantages.
It is important that the banners also harmonize visually with each other.
We liked the banner image in the attachment and it serves as inspiration.
The banner print data is produced as follows:
• Banner size: Width x Height: 3880 mm x 1880 mm
• Material: Mesh banner, PVFormat: PDF (X-3:2000)
• Fonts: converted into paths
• Trim allowance: +2 mm all around
• Color space: CMYK
• Resolution: 72 dpi (recommended) at 1:1 resolution
Look and feel
Each slider illustrates characteristics of the customer's brand and the style your logo design should communicate.

```html
<!DOCTYPE html>
<html lang="en">
<head>
<meta charset="utf-8">
<title>KalviMar – Hall Banner</title>
<link href="https://fonts.googleapis.com/css2?family=Arimo:wght@400;700&family=Fjalla+One&family=Roboto+Condensed:wght@400&display=swap" rel="stylesheet">
<style>
  :root {
    --stage: #dedede;
    --navy: #13375a;
    --lime: #96c422;
    --ink: #1d1d1b;
    --white: #ffffff;
  }
  * { margin: 0; padding: 0; box-sizing: border-box; }
  html, body { width: 1200px; height: 1200px; overflow: hidden; background: var(--stage); }
  .banner {
    position: absolute; left: 74px; top: 345px;
    width: 1052px; height: 510px;
    display: flex;
  }
  .info-panel {
    position: relative; width: 371px; height: 100%;
    background: var(--navy);
  }
  .brand-name {
    position: absolute; left: 37px; top: 26px;
    font-family: "Arimo", sans-serif; font-weight: 700;
    font-size: 64px; line-height: 1; color: var(--white);
    white-space: nowrap;
  }
  .benefits { position: absolute; left: 37px; top: 163px; list-style: none; }
  .benefit {
    display: flex; align-items: flex-start; gap: 11px; margin-bottom: 20px;
    font-family: "Roboto Condensed", sans-serif; font-weight: 400;
    font-size: 32px; line-height: 31px; color: var(--white);
  }
  .benefit svg { flex: none; width: 27px; height: 27px; margin-top: 3px; }
  .contact-band {
    position: absolute; left: 0; top: 373px; width: 100%; height: 118px;
    background: var(--lime); padding: 11px 0 0 36px;
    font-family: "Arimo", sans-serif; color: var(--ink); white-space: nowrap;
  }
  .contact-phone { font-weight: 700; font-size: 42.5px; line-height: 46px; }
  .contact-web { font-weight: 400; font-size: 40px; line-height: 40px; }
  .visual-panel { position: relative; flex: 1; height: 100%; }
  .scene {
    position: absolute; inset: 0;
    background: linear-gradient(180deg, #3f8bd0 0%, #8cbde6 42%, #b9d0c4 55%, #6f9a3c 66%, #5a7f6a 78%, #7a9a48 100%);
  }
  .headline-band {
    position: absolute; left: 0; right: 0; top: 14px; height: 117px;
    background: var(--lime); padding: 18px 0 0 37px;
    font-family: "Fjalla One", sans-serif; font-size: 31px; line-height: 40px; color: var(--ink);
  }
</style>
</head>
<body>
  <div class="banner">
    <section class="info-panel">
      <div class="brand-name">KalviMar</div>
      <ul class="benefits">
        <li class="benefit"><svg viewBox="0 0 28 28"><circle cx="13" cy="15" r="10.5" fill="none" stroke="#96c422" stroke-width="2.6"/><path d="M8 14.5l4.5 4.5L25 5" fill="none" stroke="#96c422" stroke-width="3.2" stroke-linecap="round" stroke-linejoin="round"/></svg><span>100% organic</span></li>
        <li class="benefit"><svg viewBox="0 0 28 28"><circle cx="13" cy="15" r="10.5" fill="none" stroke="#96c422" stroke-width="2.6"/><path d="M8 14.5l4.5 4.5L25 5" fill="none" stroke="#96c422" stroke-width="3.2" stroke-linecap="round" stroke-linejoin="round"/></svg><span>Individually planned</span></li>
        <li class="benefit"><svg viewBox="0 0 28 28"><circle cx="13" cy="15" r="10.5" fill="none" stroke="#96c422" stroke-width="2.6"/><path d="M8 14.5l4.5 4.5L25 5" fill="none" stroke="#96c422" stroke-width="3.2" stroke-linecap="round" stroke-linejoin="round"/></svg><span>Over 20 years of<br>experience</span></li>
      </ul>
      <div class="contact-band">
        <div class="contact-phone">04627 3150962</div>
        <div class="contact-web">www.kalvimar.de</div>
      </div>
    </section>
    <section class="visual-panel">
      <div class="scene" role="img" aria-label="Natural swimming pond with a wooden jetty, reeds and wildflowers, trees and a blue summer sky"></div>
      <div class="headline-band">Planning and construction of swimming ponds and<br>natural pools, as well as garden ponds &amp; koi ponds</div>
    </section>
  </div>
</body>
</html>
```